Revamp Marketing Website For Video Production Website

need to revamp current website www.kestrelfilmstudio.net
reference sites www.vantora.net & http://layoutcrate.net/kestrel/
Use all current content on current kestrel website. I want a revamped modenr look. Sometbing that wows customers.
reference site www.vantora.net
Target Market(s)
business owners
Industry/Entity Type
Video Production
Number of Pages Required
5+ page
Colors
Designer to choose colors to be used in the design.
Requirements
Must have
- need to revamp current website www.kestrelfilmstudio.net
- reference sites www.vantora.net & http://layoutcrate.net/kestrel/
- Use all current content on current kestrel website. I want a revamped modenr look. Sometbing that wows customers.
- reference site www.vantora.net
Nice to have
Should not have

```html
<!DOCTYPE html>
<html lang="en">
<head>
<meta charset="utf-8">
<title>Kestrel – Marketing Videos Made For You</title>
<link href="https://fonts.googleapis.com/css2?family=Bebas+Neue&family=Lato:wght@400;700&family=Oswald:wght@400;500&display=swap" rel="stylesheet">
<style>
:root{
  --blue:#13a5e8;
  --blue-dark:#0b86c2;
  --ink:#1c1f26;
  --text:#5b6068;
  --muted:#8a8f96;
  --light:#f2f3f4;
  --line:#e2e4e7;
  --footer:#1d2230;
  --white:#fff;
}
*{box-sizing:border-box;margin:0;padding:0}
html,body{width:1200px;height:4501px;overflow:hidden}
body{position:relative;background:var(--white);font-family:"Lato",sans-serif;color:var(--text)}
.abs{position:absolute}
.display{font-family:"Bebas Neue",sans-serif;font-weight:400;line-height:1}
.eyebrow{font-family:"Oswald",sans-serif;font-size:11px;letter-spacing:3.5px;color:var(--ink);text-transform:uppercase;font-weight:500}
.btn{position:absolute;display:flex;align-items:center;justify-content:center;font-family:"Oswald",sans-serif;font-size:12px;letter-spacing:3px;text-transform:uppercase;color:var(--white);background:var(--blue)}
.photo{position:absolute}
.center{left:0;width:1200px;text-align:center}

/* hero */
.hero{left:0;top:0;width:1200px;height:667px;background:radial-gradient(ellipse at 50% 30%,#1b4f8a 0%,#0f2d58 45%,#070f22 100%)}
.logo{display:flex;flex-direction:column}
.logo-name{font-family:"Bebas Neue",sans-serif;font-size:42px;letter-spacing:6px;color:var(--white);line-height:.9}
.logo-tag{font-family:"Oswald",sans-serif;font-size:10px;letter-spacing:1.2px;color:var(--white)}
.nav{display:flex;gap:26px;align-items:center;font-family:"Oswald",sans-serif;font-size:10px;color:var(--white);letter-spacing:.3px}
.nav .active{border:1px solid var(--blue);padding:7px 10px}
.hero-title{color:var(--blue);font-size:98px;line-height:.97}
.hero-sub{font-family:"Oswald",sans-serif;font-size:30px;letter-spacing:9px;color:var(--white)}
.btn.outline{background:transparent;border:2px solid var(--blue);color:var(--blue)}

/* intro */
.section-title{color:var(--blue);font-size:46px}
.lead{font-size:14.5px;line-height:1.55;color:var(--text)}
.framed{position:absolute;background:var(--blue)}
.framed .photo{left:9px;top:9px;right:9px;bottom:9px;background:linear-gradient(135deg,#3e4b58,#a9b2ba 55%,#4b5560)}

.band{left:0;top:1032px;width:1040px;height:348px;background:var(--light)}
.social-grid{display:grid;grid-template-columns:repeat(4,45px);gap:23px 18px}
.social-grid span{width:45px;height:45px;border-radius:6px;background:var(--blue)}

/* marketing */
.video{position:absolute;width:337px;height:225px}
.promo-card{position:absolute;width:151px;height:215px;background:var(--white);border:1px solid var(--line);padding:18px 14px}
.promo-card h3{font-family:"Bebas Neue",sans-serif;font-weight:400;font-size:21px;line-height:1;color:var(--ink);margin-bottom:14px}
.promo-card h3.hl{color:var(--blue)}
.promo-card li{list-style:none;font-size:11px;color:var(--muted);margin-bottom:17px}

/* features */
.features{left:0;top:2152px;width:1200px;height:752px;background:linear-gradient(180deg,#3a4454 0%,#262c36 60%,#1b1f27 100%)}
.feature{position:absolute;width:279px;height:202px;background:var(--white);padding:18px 14px}
.feature.hl{background:var(--blue);color:var(--white)}
.feature h3{font-family:"Bebas Neue",sans-serif;font-weight:400;font-size:21px;color:var(--ink);line-height:1;width:200px;white-space:nowrap;overflow:hidden;text-overflow:ellipsis}
.feature.hl h3{color:var(--white)}
.feature .tag{font-size:8px;color:var(--muted);text-transform:uppercase;line-height:1.5;margin-top:5px;width:200px}
.feature.hl .tag{color:var(--white)}
.feature p{font-size:11px;line-height:1.75;margin-top:14px;width:195px}
.feature.hl p{color:var(--white)}
.feature .more{font-size:10px;color:var(--blue);margin-top:10px;display:block}
.feature.hl .more{color:var(--white)}
.feature .icon{position:absolute;right:24px;top:16px;width:36px;height:36px;border:2px solid var(--blue);border-radius:4px;display:flex;align-items:center;justify-content:center;background:var(--white)}
.feature.hl .icon{border-color:var(--white);background:var(--blue)}
.feature .icon::after{content:"";position:absolute;left:36px;top:15px;width:26px;height:1px;background:var(--blue)}
.feature.hl .icon::after{background:var(--white)}

/* sizes */
.tile{position:absolute;overflow:hidden}
.tile .label{position:absolute;left:0;right:0;bottom:0;height:60px;display:flex;align-items:flex-end;justify-content:center;padding-bottom:14px;font-family:"Oswald",sans-serif;font-size:12px;letter-spacing:2px;color:var(--white);background:linear-gradient(180deg,transparent,rgba(0,0,0,.85))}

/* faq */
.faq{position:absolute;width:279px;height:206px;border:2px solid var(--line);padding:20px 14px;background:var(--white)}
.faq h4{font-family:"Oswald",sans-serif;font-weight:500;font-size:11px;letter-spacing:2.5px;color:var(--ink);line-height:1.7;min-height:38px}
.faq p{font-size:10.5px;line-height:1.8;margin-top:10px}
.faq .more{font-size:10px;color:var(--blue);margin-top:6px;display:block}

/* pricing */
.pricing{left:0;top:4053px;width:1200px;height:184px;border-top:1px solid var(--line)}

/* footer */
.footer{left:0;top:4237px;width:1200px;height:264px;background:var(--footer);color:#d9dce2}
.footer-head{font-family:"Lato",sans-serif;font-weight:700;font-size:13px;color:var(--blue)}
.footer-txt{font-size:11px;line-height:1.75;color:#d9dce2}
.footer-list{list-style:none;font-size:11px;line-height:24px;color:#d9dce2}
.contact-row{display:flex;gap:12px;align-items:flex-start;font-size:11px;line-height:1.45;color:#d9dce2}
.circles{display:flex;gap:12px}
.circles span{width:36px;height:36px;border-radius:50%;background:var(--blue)}
.copyright{left:0;top:4464px;width:1200px;height:37px;border-top:1px solid #2e3444;text-align:center;font-size:11px;line-height:30px;color:#cfd3da}
</style>
</head>
<body>

<!-- Hero -->
<section class="abs hero" role="img" aria-label="Film studio with lighting rigs and cameras on tripods in blue light"></section>
<div class="abs logo" style="left:161px;top:20px">
  <span class="logo-name">KESTREL</span>
  <span class="logo-tag">MARKETING VIDEOS MADE FOR YOU</span>
</div>
<nav class="abs nav" style="left:686px;top:26px">
  <span class="active">HOME</span><span>HOW IT WORKS</span><span>EXAMPLES</span><span>FAQ</span><span>PRICING</span><span>CONTACT US</span>
</nav>
<h1 class="abs display hero-title center" style="top:168px">ATTENTION GRABBING<br>VIDEO ADS</h1>
<div class="abs hero-sub center" style="top:364px">DELIVERED IN 24 HOURS!</div>
<a class="btn" style="left:452px;top:428px;width:137px;height:52px;font-size:14px">Sign up now</a>
<a class="btn outline" style="left:611px;top:428px;width:135px;height:52px;font-size:14px">Login now</a>

<!-- Promote -->
<div class="abs eyebrow" style="left:162px;top:729px">Anywhere on the web</div>
<h2 class="abs display section-title" style="left:162px;top:752px">PROMOTE ANYTHING</h2>
<p class="abs lead" style="left:162px;top:818px;width:430px">Still using static image ads with Facelink, Pixgram, Linkora, Snapwave advertising platforms? Turn them into VIDEO ADS and get higher conversion rates instantly.</p>
<a class="btn" style="left:161px;top:930px;width:113px;height:36px;font-size:11px">View more</a>
<div class="framed" style="left:611px;top:720px;width:387px;height:262px">
  <div class="photo" role="img" aria-label="Camera crew filming on a city street"></div>
</div>

<!-- Award band -->
<div class="abs band"></div>
<div class="photo" style="left:490px;top:1032px;width:550px;height:348px;background:linear-gradient(90deg,rgba(242,243,244,1) 0%,rgba(160,166,172,.7) 30%,#6d747b 70%,#4a5057 100%)" role="img" aria-label="Operator preparing a camera drone on a grassy field"></div>
<div class="abs eyebrow" style="left:162px;top:1103px">Marketing videos to use all over the web</div>
<h2 class="abs display section-title" style="left:162px;top:1126px">WE CREATE AWARD WINNING PROMOTIONAL</h2>
<div class="abs social-grid" style="left:161px;top:1216px">
  <span></span><span></span><span></span><span></span>
  <span></span><span></span><span></span><span></span>
</div>

<!-- Our marketing -->
<div class="abs eyebrow center" style="top:1449px">View our video production</div>
<h2 class="abs display section-title center" style="top:1472px">OUR MARKETING</h2>

<div class="video" style="left:161px;top:1581px;background:linear-gradient(135deg,#2d3a44,#55606a 50%,#2a2f35)" role="img" aria-label="Promo video still of a glass office lobby"></div>
<div class="video" style="left:610px;top:1581px;background:linear-gradient(135deg,#1d1f22,#4a4632 55%,#1b1c1f)" role="img" aria-label="Promo video still with a yellow title card"></div>
<div class="video" style="left:161px;top:1866px;background:linear-gradient(135deg,#3a3d42,#8d9096 55%,#6f7278)" role="img" aria-label="Promo video still of a businessman in a bright office"></div>
<div class="video" style="left:610px;top:1866px;background:linear-gradient(135deg,#4b4f52,#7c8083 50%,#3a3d3f)" role="img" aria-label="Promo video still of a man in a misty forest"></div>
<svg class="abs" style="left:301px;top:1667px" width="56" height="56" viewBox="0 0 56 56"><circle cx="28" cy="28" r="27" fill="#fff" opacity=".9"/><path d="M22 17 L40 28 L22 39Z" fill="#13a5e8"/></svg>
<svg class="abs" style="left:750px;top:1667px" width="56" height="56" viewBox="0 0 56 56"><circle cx="28" cy="28" r="27" fill="#000" opacity=".85"/><path d="M22 17 L40 28 L22 39Z" fill="#fff"/></svg>
<svg class="abs" style="left:301px;top:1952px" width="56" height="56" viewBox="0 0 56 56"><circle cx="28" cy="28" r="27" fill="#000" opacity=".85"/><path d="M22 17 L40 28 L22 39Z" fill="#fff"/></svg>
<svg class="abs" style="left:750px;top:1952px" width="56" height="56" viewBox="0 0 56 56"><circle cx="28" cy="28" r="27" fill="#000" opacity=".85"/><path d="M22 17 L40 28 L22 39Z" fill="#fff"/></svg>

<div class="promo-card" style="left:438px;top:1623px"><h3 class="hl">MARKETING PROMO 1</h3><ul><li>Marketing</li><li>Real Estate</li><li>Cristmas Celebration</li><li>Halloween Day</li></ul></div>
<div class="promo-card" style="left:889px;top:1623px"><h3>MARKETING PROMO 2</h3><ul><li>Labor Day</li><li>Memorial Day</li><li>Finess</li><li>Thanksgiving Day</li></ul></div>
<div class="promo-card" style="left:438px;top:1908px"><h3>MARKETING PROMO 3</h3><ul><li>Finess</li><li>Summer Vacation</li><li>Valentines Day</li><li>Insurance</li></ul></div>
<div class="promo-card" style="left:889px;top:1908px"><h3>MARKETING PROMO 4</h3><ul><li>Pets Bussiness</li><li>Restaurants</li><li>Retails</li><li>Game Day</li></ul></div>

<!-- Features -->
<section class="abs features" role="img" aria-label="Dim film set with a camera crew in the background"></section>
<div class="abs eyebrow center" style="top:2222px;color:#fff">We are provide best services</div>
<h2 class="abs display section-title center" style="top:2246px">OUR FEATURES</h2>

<div class="feature" style="left:161px;top:2332px">
  <h3>DONE FOR YOU</h3><div class="tag">You don't lift a finger!</div>
  <p>We make it super affordable and we Do it all for you. You'll receive a fully packaged, professionally...</p>
  <span class="more">Read More →</span>
  <div class="icon"><svg width="18" height="18" viewBox="0 0 18 18"><path d="M3 9l4 4 8-9" stroke="#13a5e8" stroke-width="2.4" fill="none"/></svg></div>
</div>
<div class="feature hl" style="left:461px;top:2332px">
  <h3>PREMIUM CONTENT</h3><div class="tag">Your business will look super high end &amp; professional</div>
  <p>We have access to millions of premium video clips, fully packaged by Award Winning Videographer...</p>
  <span class="more">Read More →</span>
  <div class="icon"><svg width="18" height="18" viewBox="0 0 18 18"><circle cx="9" cy="7" r="5" stroke="#fff" stroke-width="2" fill="none"/><path d="M6 11l-1 6 4-2 4 2-1-6" stroke="#fff" stroke-width="2" fill="none"/></svg></div>
</div>
<div class="feature" style="left:760px;top:2332px">
  <h3>FULLY LICENSED TO YOU</h3><div class="tag">You own all the videos to use forever - consider them assets!</div>
  <p>The videos are your property and come with a lifetime license for unlimited sharing and use. Th...</p>
  <span class="more">Read More →</span>
  <div class="icon"><svg width="18" height="18" viewBox="0 0 18 18"><rect x="3" y="1" width="12" height="16" stroke="#13a5e8" stroke-width="2" fill="none"/><path d="M6 6h6M6 10h6M6 14h4" stroke="#13a5e8" stroke-width="1.6"/></svg></div>
</div>
<div class="feature" style="left:161px;top:2558px">
  <h3>PERFECT LENGTH FOR VIDEO ADS</h3><div class="tag">Stand out from the crowd with video marketing</div>
  <p>Our Videos Ads range from 10 seconds to 30 seconds in length with 15 seconds being the sweet sp...</p>
  <span class="more">Read More →</span>
  <div class="icon"><svg width="20" height="16" viewBox="0 0 20 16"><rect x="1" y="2" width="13" height="12" stroke="#13a5e8" stroke-width="2" fill="none"/><path d="M14 6l5-3v10l-5-3" stroke="#13a5e8" stroke-width="2" fill="none"/></svg></div>
</div>
<div class="feature" style="left:461px;top:2558px">
  <h3>SOCIAL VIDEO COVER</h3><div class="tag">"Wow" customers with a beautiful designed social cover video...</div>
  <p>We can convert any video to a Facelink Video Cover for your FL Business page. Additional fees m...</p>
  <span class="more">Read More →</span>
  <div class="icon"><svg width="18" height="18" viewBox="0 0 18 18"><rect x="2" y="5" width="14" height="11" stroke="#13a5e8" stroke-width="2" fill="none"/><path d="M2 5l3-4h10l-3 4" stroke="#13a5e8" stroke-width="2" fill="none"/></svg></div>
</div>
<div class="feature" style="left:760px;top:2558px">
  <h3>BEST SUPPORT</h3><div class="tag">We are available to you at all times for any kind of support</div>
  <p>Reach out anytime, anywhere. Our team of tech, marketing and video experts are here to help you...</p>
  <span class="more">Read More →</span>
  <div class="icon"><svg width="18" height="18" viewBox="0 0 18 18"><circle cx="9" cy="9" r="7" stroke="#13a5e8" stroke-width="2" fill="none"/><path d="M9 5v4l3 2" stroke="#13a5e8" stroke-width="2" fill="none"/></svg></div>
</div>
<a class="btn" style="left:543px;top:2797px;width:114px;height:37px;font-size:11px">View more</a>

<!-- Video sizes -->
<div class="abs eyebrow center" style="top:2962px">View our different video sizes</div>
<h2 class="abs display section-title center" style="top:2986px">VIDEO SIZES AVAILABLE</h2>
<div class="tile" style="left:161px;top:3084px;width:428px;height:246px;background:linear-gradient(135deg,#8a7a68,#c9b39a 50%,#6b5e52)" role="img" aria-label="Smiling couple in sun hats on a city street"><div class="label">WIDE SCREEN VIDEOS</div></div>
<div class="tile" style="left:161px;top:3353px;width:202px;height:202px;background:linear-gradient(135deg,#3f474f,#9aa3ab 60%,#555c63)" role="img" aria-label="Film camera crew on a foggy street"><div class="label">SQUARE SCREEN VIDEOS</div></div>
<div class="tile" style="left:386px;top:3353px;width:203px;height:202px;background:linear-gradient(135deg,#c9cdd0,#e8eaeb 50%,#8d9297)" role="img" aria-label="Two men playing football in the mist"><div class="label">SQUARE SCREEN VIDEOS</div></div>
<div class="tile" style="left:611px;top:3084px;width:203px;height:471px;background:linear-gradient(180deg,#3c6a8a,#4f8c8f 40%,#8b5466 70%,#2e2f38)" role="img" aria-label="Colourful painted building on a street corner"><div class="label">VERTICAL SCREEN VIDEOS</div></div>
<div class="tile" style="left:837px;top:3084px;width:203px;height:471px;background:linear-gradient(180deg,#5a6d84,#b3c0cf 45%,#6f7a86)" role="img" aria-label="Hand holding a phone by an airplane window"><div class="label">VERTICAL SCREEN VIDEOS</div></div>

<!-- FAQ -->
<div class="abs eyebrow center" style="top:3610px">Clear your doubt</div>
<h2 class="abs display section-title center" style="top:3634px">FREQUNTLY ASKED QUESTIONS</h2>
<div class="faq" style="left:161px;top:3718px">
  <h4>HOW DOES THIS WORK?</h4>
  <p>You can purchase video ads on an "as needed" basis or you can choose to sign up for a subscription that provides a significant savings per video ad and provides you with new updated video ads each and every month.</p>
  <span class="more">Read More →</span>
</div>
<div class="faq" style="left:461px;top:3718px">
  <h4>CAN I USE THE VIDEO ADS AFTER MY SUBSCRIPTION IS OVER?</h4>
  <p>Yes. All the video ads that you paid for are yours to keep, forever. You own the final Mp4 HD files. You have full control over your account. You can reactivate your subscription at any time and can even downgrade and upgrade the.</p>
  <span class="more">Read More →</span>
</div>
<div class="faq" style="left:760px;top:3718px">
  <h4>WHERE CAN I POST THE VIDEO ADS I DOWNLOAD?</h4>
  <p>You can post, publish, upload, and share your video ads on Facelink, Pixgram, Viewtube, Chirper, Websites, Snapwave, Linkora, Blogs and anywhere else on the web as much as you want.</p>
  <span class="more">Read More →</span>
</div>
<a class="btn" style="left:543px;top:3967px;width:114px;height:37px;font-size:11px">Read more</a>

<!-- Pricing -->
<section class="abs pricing"></section>
<h2 class="abs display" style="left:162px;top:4088px;font-size:36px;color:var(--blue)">EXPLORE OUR PACKAGES &amp; PRICING</h2>
<p class="abs" style="left:162px;top:4130px;width:480px;font-size:11px;line-height:1.7">Videos Compatible w/ Blogs, Websites and anywhere else on the web, Seasonal Videos Included Spring, Summer, Fall, Winter, Video Length etc....</p>
<a class="btn" style="left:814px;top:4107px;width:226px;height:37px;font-size:11px;letter-spacing:2.5px">View our prices &amp; packeges</a>

<!-- Footer -->
<footer class="abs footer"></footer>
<div class="abs logo" style="left:161px;top:4266px">
  <span class="logo-name">KESTREL</span>
  <span class="logo-tag">MARKETING VIDEOS MADE FOR YOU</span>
</div>
<p class="abs footer-txt" style="left:162px;top:4328px;width:200px">With Kestrel, you simply let us know what you want to promote and we will have your video ad finished as soon as 24 hours!</p>

<h5 class="abs footer-head" style="left:388px;top:4262px">Contact Info</h5>
<div class="abs contact-row" style="left:388px;top:4292px">
  <svg width="14" height="14" viewBox="0 0 14 14"><path d="M3 1l3 3-2 2a8 8 0 0 0 4 4l2-2 3 3-2 2C6 13 1 8 1 3z" fill="#fff"/></svg><span>+1-555-014-2290</span>
</div>
<div class="abs contact-row" style="left:388px;top:4326px">
  <svg width="14" height="12" viewBox="0 0 14 12"><rect x="1" y="1" width="12" height="10" stroke="#fff" stroke-width="1.4" fill="none"/><path d="M1 1l6 5 6-5" stroke="#fff" stroke-width="1.4" fill="none"/></svg><span>support@kestrelfilmstudio.<br>net</span>
</div>
<div class="abs contact-row" style="left:388px;top:4374px">
  <svg width="14" height="18" viewBox="0 0 14 18"><path d="M7 1a6 6 0 0 1 6 6c0 4-6 10-6 10S1 11 1 7a6 6 0 0 1 6-6z" fill="#fff"/><circle cx="7" cy="7" r="2.2" fill="#1d2230"/></svg><span>1470 Harbor Vista Dr<br>Bayview, CA 90000</span>
</div>

<h5 class="abs footer-head" style="left:611px;top:4262px">Sitemap</h5>
<ul class="abs footer-list" style="left:611px;top:4286px"><li>Home</li><li>Examples</li><li>Faq</li><li>Pricing</li><li>Contact Us</li></ul>
<ul class="abs footer-list" style="left:709px;top:4286px"><li>How It Works</li><li>Term Of Service</li><li>Privacy Policy</li><li>Cookies Policy</li></ul>

<h5 class="abs footer-head" style="left:838px;top:4262px">Follow Us On</h5>
<div class="abs circles" style="left:838px;top:4296px"><span></span><span></span><span></span><span></span></div>

<div class="abs copyright">Copyright © 2019 <b>Kestrel Video</b>. All Right Reserved. | Terms &amp; Conditons.</div>

</body>
</html>
```